Business Card - connecting 2 souls and beggining the journey of self discovery

Logo on the front
with tag line

On the back list of services and contact details

Seminars
workshops
Coaching
podcasts

Darren Whitlow
Health & Wellbeing Life Coach
0491 372 615
darren@brightcoreliving.example
brightcoreliving.example

Industry/Entity Type

Life Coaching

Contact Information for Business Card

I like the use of colour from the logo to be used. I'm not a fan of white.

Requirements
Must have
• My tagline: The journey home starts with you
Nice to have
• Use of colour that is in the mind body soul logo

```html
<!DOCTYPE html>
<html lang="en">
<head>
<meta charset="utf-8">
<title>Brightcore Living – Business Card</title>
<link rel="stylesheet" href="https://fonts.googleapis.com/css2?family=Montserrat:wght@500&family=Open+Sans:wght@400;600;700&display=swap">
<style>
  :root {
    --backdrop: #2b2b2d;
    --card-grey: #77787b;
    --card-grey-light: #8a8b8e;
    --card-white: #f7f7f6;
    --brand-grey: #6e6f72;
    --brand-grey-light: #e6e6e6;
    --green: #3fae6e;
    --teal: #2aa58a;
    --pink: #ea4f6a;
    --orange: #f39a2c;
    --lime: #8cc63f;
    --ink: #5b5c5f;
    --mark: #ec6a5c;
  }
  * { box-sizing: border-box; margin: 0; padding: 0; }
  html, body { width: 1200px; height: 960px; overflow: hidden; }
  body {
    background: var(--backdrop);
    display: flex;
    flex-direction: column;
    align-items: center;
    justify-content: center;
    gap: 48px;
    font-family: "Open Sans", Arial, sans-serif;
  }
  .card {
    position: relative;
    width: 720px;
    height: 411px;
    border-radius: 4px;
    overflow: hidden;
    box-shadow: 0 10px 28px rgba(0,0,0,0.45);
  }

  /* Back of card */
  .card--back {
    background: linear-gradient(160deg, var(--card-grey-light), var(--card-grey));
    display: flex;
    flex-direction: column;
    align-items: center;
    justify-content: center;
    gap: 20px;
  }
  .brand-mark {
    width: 74px;
    height: 74px;
    border-radius: 50%;
    background: var(--mark);
  }
  .brand-name {
    font-family: "Montserrat", Arial, sans-serif;
    font-weight: 500;
    letter-spacing: -0.5px;
  }
  .card--back .brand-name {
    color: var(--brand-grey-light);
    font-size: 34px;
  }
  .services {
    list-style: none;
    display: flex;
    gap: 10px;
    color: var(--brand-grey-light);
    font-size: 15px;
  }
  .services li + li::before {
    content: "";
    display: inline-block;
    width: 6px;
    height: 6px;
    border-radius: 50%;
    background: var(--green);
    margin-right: 10px;
    vertical-align: middle;
  }

  /* Front of card */
  .card--front { background: var(--card-white); }
  .identity {
    position: absolute;
    right: 52px;
    top: 70px;
    display: flex;
    flex-direction: column;
    align-items: flex-end;
  }
  .identity .brand-mark {
    width: 70px;
    height: 70px;
    margin-right: 54px;
    margin-bottom: 12px;
  }
  .card--front .brand-name {
    color: var(--brand-grey);
    font-size: 27px;
    line-height: 1.1;
  }
  .tagline {
    color: var(--brand-grey);
    font-weight: 600;
    font-size: 15.5px;
    margin-top: 2px;
  }
  .person {
    position: absolute;
    left: 48px;
    top: 200px;
  }
  .person__name {
    color: var(--green);
    font-weight: 700;
    font-size: 21px;
    text-transform: uppercase;
    letter-spacing: 0.2px;
  }
  .person__role {
    color: var(--pink);
    font-weight: 700;
    font-size: 16.5px;
    text-transform: uppercase;
    margin-bottom: 10px;
  }
  .contacts { list-style: none; }
  .contacts li {
    display: flex;
    align-items: center;
    gap: 9px;
    color: var(--ink);
    font-size: 15px;
    line-height: 22px;
  }
  .contacts svg { width: 12px; height: 12px; fill: var(--teal); flex: none; }
  .rule {
    position: absolute;
    left: 48px;
    right: 64px;
    top: 338px;
    height: 1px;
    background: var(--teal);
    opacity: 0.7;
  }
  .bands {
    position: absolute;
    left: 0; right: 0; bottom: 0;
  }
  .bands .band-pink { height: 3px; background: var(--pink); }
  .bands .band-orange { height: 3px; background: var(--orange); }
  .bands .band-green { height: 16px; background: linear-gradient(90deg, var(--teal), var(--lime) 55%, var(--teal)); }
</style>
</head>
<body>

<section class="card card--back" aria-label="Card back">
  <div class="brand-mark"></div>
  <div class="brand-name">Brightcore Living</div>
  <ul class="services">
    <li>Seminars</li>
    <li>Workshops</li>
    <li>Coaching</li>
    <li>Podcasts</li>
  </ul>
</section>

<section class="card card--front" aria-label="Card front">
  <div class="identity">
    <div class="brand-mark"></div>
    <div class="brand-name">Brightcore Living</div>
    <div class="tagline">The journey home starts with you</div>
  </div>

  <div class="person">
    <div class="person__name">Darren Whitlow</div>
    <div class="person__role">Health &amp; Wellbeing Life Coach</div>
    <ul class="contacts">
      <li>
        <svg viewBox="0 0 12 12" aria-hidden="true"><path d="M2.4 0.6l1.8 0 .7 2.6-1.3 1c.6 1.4 1.6 2.4 3 3l1-1.3 2.6.7v1.8c0 .7-.6 1.2-1.3 1.1C4.4 9.1 1.9 6.6 1.3 1.9 1.2 1.2 1.7.6 2.4.6z"/></svg>
        0491 372 615
      </li>
      <li>
        <svg viewBox="0 0 12 12" aria-hidden="true"><path d="M0 2h12v1L6 6.6 0 3z M0 4.4l6 3.6 6-3.6V10H0z"/></svg>
        darren@brightcoreliving.example
      </li>
      <li>
        <svg viewBox="0 0 12 12" aria-hidden="true"><circle cx="6" cy="6" r="6"/><path d="M0.5 6h11M6 0.5c-2.4 2.8-2.4 8.2 0 11M6 0.5c2.4 2.8 2.4 8.2 0 11" stroke="#f7f7f6" stroke-width="0.9" fill="none"/></svg>
        brightcoreliving.example
      </li>
    </ul>
  </div>

  <div class="rule"></div>

  <div class="bands">
    <div class="band-pink"></div>
    <div class="band-orange"></div>
    <div class="band-green"></div>
  </div>
</section>

</body>
</html>
```